Marwick Law Letterhead

We need a new letterhead design for a Law Firm. The address for the law firm is 1475 Calloway Street, Suite 210, Houston, Texas 77041. Phone Number: 832-361-9027; Fax Number: 832-614-7359. The logo is uploaded to the project.

```html
<!DOCTYPE html>
<html lang="en">
<head>
<meta charset="utf-8">
<title>Marwick Law Letterhead</title>
<link rel="stylesheet" href="https://fonts.googleapis.com/css2?family=Montserrat:wght@400;600&display=swap">
<style>
  :root {
    --backdrop: #e8e8e8;
    --paper: #ffffff;
    --navy: #1f2f5c;
    --red: #c8161d;
    --ink: #1a1a1a;
  }
  * { margin: 0; padding: 0; box-sizing: border-box; }
  html, body {
    width: 1154px;
    height: 1200px;
    overflow: hidden;
    background: var(--backdrop);
  }
  .letterhead {
    position: absolute;
    left: 167px;
    top: 30px;
    width: 820px;
    height: 1140px;
    background: var(--paper);
    font-family: "Montserrat", Arial, sans-serif;
  }
  .brand {
    position: absolute;
    left: 30px;
    top: 74px;
    display: flex;
    align-items: center;
    gap: 12px;
  }
  .brand-mark {
    width: 18px;
    height: 18px;
    background: var(--red);
  }
  .brand-name {
    font-size: 34px;
    font-weight: 600;
    color: var(--navy);
    letter-spacing: 0.5px;
  }
  .contact {
    position: absolute;
    left: 0;
    right: 0;
    top: 1058px;
    text-align: center;
    color: var(--ink);
    font-size: 14px;
  }
  .contact-numbers {
    display: flex;
    justify-content: center;
    gap: 12px;
    align-items: center;
  }
  .contact-item {
    display: inline-flex;
    align-items: center;
    gap: 9px;
  }
  .contact-item svg { width: 13px; height: 13px; }
  .contact-address { margin-top: 12px; }
  .contact-rule {
    width: 378px;
    height: 1px;
    margin: 8px auto 0;
    background: var(--red);
  }
</style>
</head>
<body>
  <main class="letterhead">
    <header class="brand">
      <span class="brand-mark"></span>
      <span class="brand-name">Marwick Law</span>
    </header>

    <footer class="contact">
      <div class="contact-numbers">
        <span class="contact-item">
          <svg viewBox="0 0 16 16" aria-label="Phone">
            <path fill="#c8161d" d="M3.6 1.2l2.2 2.6-1.3 1.6c.9 2.2 2.6 3.9 4.8 4.8l1.6-1.3 2.6 2.2-1.4 2.4C7 13 2.9 9 2 3.2z"/>
          </svg>
          832-361-9027
        </span>
        <span class="contact-item">
          <svg viewBox="0 0 16 16" aria-label="Fax">
            <rect x="4" y="1" width="8" height="4" fill="#c8161d"/>
            <rect x="1" y="5" width="14" height="7" rx="1.5" fill="#c8161d"/>
            <rect x="4" y="9" width="8" height="6" fill="#fff" stroke="#c8161d" stroke-width="1.4"/>
          </svg>
          832-614-7359
        </span>
      </div>
      <p class="contact-address">1475 Calloway Street, Suite 210, Houston, Texas 77041</p>
      <div class="contact-rule"></div>
    </footer>
  </main>
</body>
</html>
```